Ecard for facebook and Instagram postings

I need 4 ecards (don't know if that is what it is called) for Facebook and Instagram postings. My Logo and company name should be incorporated and also be square. I would like to be able to insert text as I need. Examples are:

https://www.plorvexa.com/photo.php?fbid=20262841672382489&set=a.20261729249182489.516031.71298967488&type=1&relevant_count=1

https://media-a-kpt.yy.plorvexacdn.net/hpics-bmk4/2345967_657092986477056_308792573_n.jpg

I don't necessarily need images on them, just the color scheme to my business cards and the logo and business name. But if you'd like to give it an interesting look, you can go ahead and play with it. My site is tornquillmentoring.com, if you'd like to see the style of it.

Thank you!!!
Updates

I just uploaded the logo in two variations.  Thank you!

Target Market(s)

Women 16-65

Industry/Entity Type

Business

Requirements
Must have
• Logo and business name
Should not have
• No white background. I have attached business card picture so you can have an idea of what I'd like.

```html
<!DOCTYPE html>
<html lang="en">
<head>
<meta charset="utf-8">
<title>Tornquill Mentoring – Quote Card</title>
<link rel="stylesheet" href="https://fonts.googleapis.com/css2?family=Tinos:wght@700&display=swap">
<style>
  :root {
    --orange: #f29a2e;
    --orange-deep: #e8641c;
    --crimson: #c4202f;
    --ink: #111111;
    --white: #ffffff;
  }
  html, body {
    margin: 0;
    padding: 0;
    overflow: hidden;
    background: var(--orange);
  }
  .card {
    position: relative;
    width: 1200px;
    height: 1200px;
    overflow: hidden;
    background: radial-gradient(circle at 50% 40%, #f5a43a 0%, var(--orange) 60%, #ef9228 100%);
    font-family: "Tinos", "Times New Roman", serif;
  }
  .top-band {
    position: absolute;
    top: 0;
    left: 0;
    width: 100%;
    height: 20px;
    background: var(--crimson);
  }
  .flourish {
    position: absolute;
    top: 30px;
    left: 370px;
    width: 460px;
    height: 48px;
    border-radius: 24px;
    background: linear-gradient(90deg, rgba(196,32,47,0) 0%, rgba(196,32,47,0.55) 30%, var(--crimson) 50%, rgba(196,32,47,0.55) 70%, rgba(196,32,47,0) 100%);
  }
  .quote-mark {
    position: absolute;
    color: var(--crimson);
    font-weight: 700;
    font-size: 260px;
    line-height: 1;
  }
  .quote-mark.open { top: 135px; left: 74px; }
  .quote-mark.close { top: 830px; left: 955px; }
  .quote-text {
    position: absolute;
    top: 208px;
    left: 60px;
    width: 1080px;
    margin: 0;
    text-align: center;
    color: var(--ink);
    font-weight: 700;
    font-size: 110px;
    line-height: 130px;
  }
  .quote-line { display: block; white-space: nowrap; }
  .footer-waves {
    position: absolute;
    left: 0;
    bottom: 0;
    width: 1200px;
    height: 230px;
  }
  .brand {
    position: absolute;
    left: 26px;
    bottom: 30px;
    color: var(--white);
    font-weight: 700;
    line-height: 1;
  }
  .brand-name {
    display: block;
    font-size: 100px;
  }
  .brand-tagline {
    display: block;
    margin-top: 12px;
    font-size: 34px;
    letter-spacing: 10px;
  }
  .brand-badge {
    position: absolute;
    right: 22px;
    bottom: 18px;
    width: 148px;
    height: 148px;
    box-sizing: border-box;
    border-radius: 50%;
    background: var(--orange-deep);
    border: 6px solid var(--white);
  }
</style>
</head>
<body>
  <main class="card">
    <div class="top-band"></div>
    <div class="flourish" role="img" aria-label="Decorative crimson flourish ornament"></div>

    <span class="quote-mark open" aria-hidden="true">&ldquo;</span>
    <p class="quote-text">
      <span class="quote-line">Ignorance is the</span>
      <span class="quote-line">curse of God;</span>
      <span class="quote-line">knowledge is the</span>
      <span class="quote-line">wing wherewith we</span>
      <span class="quote-line">fly to heaven</span>
    </p>
    <span class="quote-mark close" aria-hidden="true">&rdquo;</span>

    <svg class="footer-waves" viewBox="0 0 1200 230" aria-hidden="true">
      <path d="M0 70 C 400 40 800 10 1200 22 L1200 230 L0 230 Z" fill="var(--crimson)"/>
      <path d="M0 8 C 300 0 560 40 720 130 C 800 175 870 220 930 230 L0 230 Z" fill="var(--orange-deep)"/>
    </svg>

    <div class="brand">
      <span class="brand-name">Tornquill</span>
      <span class="brand-tagline">MENTORING</span>
    </div>
    <div class="brand-badge" aria-hidden="true"></div>
  </main>
</body>
</html>
```